TL - business card

Tallow Partners is an insurance brokerage firm, inovative, proactive, vigorous, which aims to become the leader of the insurance brokers in Anfrica. We should like to get some designs which should be avoided also in Gray / Metallic for the Administration and Orange / Blue for the Managers (ike in the picture sent). The Blue / Green logo is not the correct one, but the source of the file. Please adjust the color accordingly for the business cards. 1 / Orange / Blue 2 / Gray / Metallic We want something classic but which is transmitted strenght, inovation, modernity and most of all, rapidity. We want something start-up like, very punchy and catching eye remaining profesional at the same time. Name: Dorian Whitlock: Managing Director Address: N ° 17/18 Rua Veloso - R / C 2B Direita - Bairro Mutamba - Luanda Tel: (+244) 947 582 316 Email: dorian.whitlock@tallow-p.example Website: www.tallow-p. example We want classic in the front and creative, colorfull at the back. The cards will be printed in relief, with very high quality of paper.
Insurance Broker
Colors
Designer to choose colors to be used in the design.

```html
<!DOCTYPE html>
<html lang="en">
<head>
<meta charset="utf-8">
<title>Tallow Partners – Business Card</title>
<link rel="stylesheet" href="https://fonts.googleapis.com/css2?family=Open+Sans:wght@400;700;800&family=Cinzel:wght@400;600&display=swap">
<style>
  :root {
    --navy: #22336b;
    --orange: #f05a24;
    --orange-mid: #f47c20;
    --bright-blue: #1b75bc;
    --white: #ffffff;
    --canvas: #f2f2f2;
  }
  * { box-sizing: border-box; margin: 0; padding: 0; }
  html, body {
    width: 1200px; height: 1200px; overflow: hidden;
    background: var(--canvas);
  }
  .canvas { position: relative; width: 1200px; height: 1200px; }

  .card {
    position: absolute;
    left: 355px;
    width: 474px;
    height: 269px;
    overflow: hidden;
    color: var(--white);
  }
  .card--front { top: 154px; background: var(--navy); }
  .card--back {
    top: 747px;
    background: linear-gradient(90deg, var(--orange) 0%, var(--orange-mid) 50%, var(--orange) 100%);
  }

  .brand-mark {
    position: absolute;
    left: 50%;
    transform: translateX(-50%);
    border-radius: 50%;
  }
  .card--front .brand-mark {
    top: 42px; width: 96px; height: 96px;
    border: 6px solid var(--orange-mid);
  }
  .card--back .brand-mark {
    top: 62px; width: 78px; height: 78px;
    border: 5px solid var(--white);
  }

  .brand-name {
    position: absolute;
    left: 0; right: 0;
    text-align: center;
    font-family: "Open Sans", sans-serif;
    font-weight: 800;
    text-transform: uppercase;
    letter-spacing: 0.3px;
    line-height: 1;
  }
  .card--front .brand-name { top: 150px; font-size: 25px; color: var(--bright-blue); }
  .card--back .brand-name { top: 141px; font-size: 20px; color: var(--white); }

  .rule-row {
    position: absolute;
    left: 0; right: 0;
    display: flex;
    align-items: center;
    gap: 8px;
  }
  .rule-row::before, .rule-row::after {
    content: "";
    flex: 1;
    height: 2px;
  }
  .card--front .rule-row { top: 216px; }
  .card--front .rule-row::before, .card--front .rule-row::after { background: var(--orange); }
  .card--back .address-row { top: 215px; }
  .card--back .rule-row::before, .card--back .rule-row::after { background: var(--navy); }

  .holder-name {
    font-family: "Open Sans", sans-serif;
    font-weight: 700;
    font-size: 12.5px;
    text-transform: uppercase;
  }
  .holder-role {
    position: absolute;
    top: 235px; left: 0; right: 0;
    text-align: center;
    font-family: "Open Sans", sans-serif;
    font-size: 11px;
  }

  .address, .contact-item {
    font-family: "Cinzel", serif;
    font-size: 9px;
    display: flex;
    align-items: center;
    gap: 4px;
    white-space: nowrap;
  }
  .contact-row {
    position: absolute;
    top: 237px; left: 16px; right: 16px;
    display: flex;
    justify-content: space-between;
  }
  .icon { width: 12px; height: 12px; flex: none; }
</style>
</head>
<body>
<main class="canvas">

  <section class="card card--front" aria-label="Card front">
    <div class="brand-mark"></div>
    <div class="brand-name">Tallow-Partners</div>
    <div class="rule-row">
      <span class="holder-name">Dorian Whitlock</span>
    </div>
    <div class="holder-role">Managing Director</div>
  </section>

  <section class="card card--back" aria-label="Card back">
    <div class="brand-mark"></div>
    <div class="brand-name">Tallow-Partners</div>

    <div class="rule-row address-row">
      <span class="address">
        <svg class="icon" viewBox="0 0 12 12"><circle cx="6" cy="6" r="6" fill="#fff"/><path d="M6 2.5a2.2 2.2 0 0 0-2.2 2.2C3.8 6.4 6 9.3 6 9.3s2.2-2.9 2.2-4.6A2.2 2.2 0 0 0 6 2.5z" fill="#f05a24"/><circle cx="6" cy="4.7" r="0.9" fill="#fff"/></svg>
        N ° 17/18 Rua Veloso - R / C 2B Direita - Bairro Mutamba - Luanda
      </span>
    </div>

    <div class="contact-row">
      <span class="contact-item">
        <svg class="icon" viewBox="0 0 12 12"><path d="M3 1l2 2.5-1.2 1.3c.6 1.4 1.7 2.5 3.1 3.1L8.2 6.7 10.7 8.7 9.6 10.8C5.5 10.5 1.5 6.5 1.2 2.4z" fill="#fff"/></svg>
        (+244) 947 582 316
      </span>
      <span class="contact-item">
        <svg class="icon" viewBox="0 0 12 12"><rect x="1" y="3" width="10" height="6.5" fill="#fff"/><path d="M1 3l5 3.6L11 3" fill="none" stroke="#f05a24" stroke-width="0.9"/></svg>
        dorian.whitlock@tallow-p.example
      </span>
      <span class="contact-item">
        <svg class="icon" viewBox="0 0 12 12"><circle cx="6" cy="6" r="5" fill="none" stroke="#fff" stroke-width="1.1"/><ellipse cx="6" cy="6" rx="2.2" ry="5" fill="none" stroke="#fff" stroke-width="0.9"/><path d="M1 6h10M2 3.5h8M2 8.5h8" stroke="#fff" stroke-width="0.8"/></svg>
        www.tallow-p. example
      </span>
    </div>
  </section>

</main>
</body>
</html>
```